New Banner Ad Design Project

We are a start-up in San Francisco that sells consignment clothes with a percentage of the proceeds donated to charity. Also, volunteer groups can conduct dress drives and send them to us and we will sell them and give their charity back 60% of the proceeds.

We have several uses for banners:
- Home page banner:
- Promote timely Flash Sales (they last only 96 hours) which happen 2x/week
- Promote how good it feels to give back and shop
- Promote any special promotions such as a Gift With Purchase
- Community banner:
- Promote the lifestyle
- Promote any particular group conducting a dress drive

If you are going to submit one banner it is to be for an upcoming sale, as the two attached files address (maternity sale). If we find the right designer we will consider working with them beyond the design contest for future sale banners as well as others

We consider our 'competitors' to be The Garment Venture, The TrueCloset, WeavTurn, KnitRise, WearAgain. Our key differentiator is the charitable components and how groups are conducting dress drives to raise money.

We are in the midst of changing our company name, tagline and logo. The new company will be called 'LunaTessa' and our tagline is 'Rewoven Kindness'

Target Market(s)

Our initial audience is young women 16 - 30. We will be focusing on Prom February through May which appeals to 16 - 18 year olds.

We also have maternity-wear. We want these women to feel fashionable

We are focused on individuals who want to give back.

Industry/Entity Type

Charity

Font styles to use
Serif
Sans Serif

Colors
8769ae
1b1b1b
474747
c3c3c3
86cfc6
b7a5cd

Requirements
Must have
• - Youthful and stylish voice (not to be confused with Young)
- Appealing visuals
- Powerful call-to-action as it pertains to banners for our flash sales
- An inclusive feel
- Communicates our charitable component
Nice to have
• - Emotional appeal
- Women wearing our clothes (see attached)
Should not have
• - Too much text
- Too girly; overly flowery

```html
<!DOCTYPE html>
<html lang="en">
<head>
<meta charset="utf-8">
<title>LunaTessa – Shop and Give Back</title>
<link rel="stylesheet" href="https://fonts.googleapis.com/css2?family=Didact+Gothic&family=Cormorant+Garamond:ital,wght@1,600&family=Oswald:wght@500&display=swap">
<style>
  :root {
    --plum: #5a2b6f;
    --plum-deep: #4a2060;
    --teal: #86cfc6;
    --teal-dark: #6fbcb2;
    --lavender: #b7a5cd;
    --lavender-light: #d9cde6;
    --ink: #1b1b1b;
    --grey: #474747;
    --silver: #c3c3c3;
    --paper: #ffffff;
    --brand-plum: #4e2563;
  }
  html, body {
    margin: 0;
    padding: 0;
    overflow: hidden;
    background: #f2f2f2;
  }
  .banner {
    position: relative;
    width: 1200px;
    height: 553px;
    overflow: hidden;
    background: radial-gradient(ellipse at 70% 40%, #63327a 0%, var(--plum) 55%, var(--plum-deep) 100%);
    font-family: "Didact Gothic", sans-serif;
  }
  .photo-card {
    position: absolute;
    box-sizing: border-box;
    padding: 9px;
    background: var(--paper);
    box-shadow: 4px 6px 14px rgba(0,0,0,0.45);
  }
  .photo-card .photo {
    width: 100%;
    height: 100%;
  }
  .photo-card--maternity {
    left: 34px;
    top: 12px;
    width: 340px;
    height: 530px;
    transform: rotate(-4.5deg);
  }
  .photo-card--maternity .photo {
    background: linear-gradient(170deg, #c9c7c0 0%, #8d8a80 35%, #b9ada0 60%, #d8cfc3 100%);
  }
  .photo-card--accessories {
    left: 303px;
    top: 46px;
    width: 356px;
    height: 465px;
    transform: rotate(6deg);
  }
  .photo-card--accessories .photo {
    background: linear-gradient(160deg, #efeeea 0%, #dcdad6 40%, #3a3a3c 62%, #1b1b1b 100%);
  }
  .photo-caption {
    position: absolute;
    font-family: "Cormorant Garamond", serif;
    font-style: italic;
    font-weight: 600;
    color: var(--ink);
    line-height: 0.95;
  }
  .photo-caption--maternity {
    left: 52px;
    bottom: 28px;
    font-size: 26px;
  }
  .photo-caption--maternity span { display: block; padding-left: 18px; }
  .photo-caption--accessories {
    left: 22px;
    top: 14px;
    font-size: 22px;
  }
  .headline {
    position: absolute;
    left: 0;
    top: 0;
    width: 1200px;
    height: 553px;
    pointer-events: none;
  }
  .headline text { font-family: "Didact Gothic", sans-serif; }
  .headline .word-main { fill: var(--teal); font-size: 117px; }
  .headline .word-and { fill: var(--lavender); font-size: 72px; }
  .headline .subline { fill: var(--lavender-light); font-size: 23px; }
  .cta {
    position: absolute;
    left: 701px;
    top: 305px;
    width: 228px;
    height: 80px;
    display: flex;
    align-items: center;
    gap: 8px;
    padding-left: 14px;
    box-sizing: border-box;
    background: linear-gradient(180deg, #9adbd2 0%, var(--teal) 55%, var(--teal-dark) 100%);
    border-radius: 4px;
    transform: rotate(-1.5deg);
    box-shadow: 2px 4px 8px rgba(0,0,0,0.35);
    text-decoration: none;
  }
  .cta-label {
    font-family: "Oswald", sans-serif;
    font-weight: 500;
    font-size: 36px;
    letter-spacing: -0.5px;
    color: var(--brand-plum);
    transform: scaleX(0.88);
    transform-origin: left center;
  }
  .cta-icon { width: 44px; height: 44px; margin-left: -14px; }
  .page-curl {
    position: absolute;
    left: 0;
    top: 0;
    width: 1200px;
    height: 553px;
  }
  .brand {
    position: absolute;
    left: 886px;
    top: 470px;
    width: 300px;
    height: 76px;
  }
  .brand-name {
    position: absolute;
    left: 0;
    top: 0;
    font-family: "Didact Gothic", sans-serif;
    font-size: 46px;
    letter-spacing: 1px;
    color: var(--brand-plum);
    line-height: 1;
  }
  .brand-tagline {
    position: absolute;
    left: 2px;
    top: 58px;
    font-family: "Didact Gothic", sans-serif;
    font-size: 11px;
    letter-spacing: 1px;
    color: var(--grey);
  }
</style>
</head>
<body>
<div class="banner">

  <div class="photo-card photo-card--maternity">
    <div class="photo" role="img" aria-label="Photo of a woman in a patterned maternity dress with a grey sash, standing on a tree-lined city path"></div>
    <div class="photo-caption photo-caption--maternity">Maternity<span>Wear</span></div>
  </div>

  <div class="photo-card photo-card--accessories">
    <div class="photo" role="img" aria-label="Photo of a woman in sunglasses, a black jacket and a layered black beaded necklace"></div>
    <div class="photo-caption photo-caption--accessories">Accessories</div>
  </div>

  <svg class="headline" viewBox="0 0 1200 553" aria-label="Shop and give back. Portion of all sales is donated to charity">
    <text class="word-main" x="718" y="116" textLength="262" lengthAdjust="spacingAndGlyphs">SHOP</text>
    <text class="word-and" x="1018" y="108" textLength="132" lengthAdjust="spacingAndGlyphs">and</text>
    <text class="word-main" x="676" y="212" textLength="514" lengthAdjust="spacingAndGlyphs">GIVE BACK</text>
    <text class="subline" x="685" y="269" textLength="505" lengthAdjust="spacingAndGlyphs">Portion of all sales is donated to charity</text>
  </svg>

  <a class="cta" href="#">
    <span class="cta-label">SHOP NOW</span>
    <svg class="cta-icon" viewBox="0 0 44 44" aria-hidden="true">
      <circle cx="22" cy="22" r="20" fill="#ffffff"/>
      <path d="M16 11 L33 22 L16 33 L20 22 Z" fill="#5a2b6f"/>
    </svg>
  </a>

  <svg class="page-curl" viewBox="0 0 1200 553" aria-hidden="true">
    <defs>
      <linearGradient id="flapShade" x1="0" y1="1" x2="1" y2="0">
        <stop offset="0" stop-color="#ffffff"/>
        <stop offset="0.6" stop-color="#dcdcdc"/>
        <stop offset="1" stop-color="#9a9a9a"/>
      </linearGradient>
      <linearGradient id="curlShadow" x1="0" y1="0" x2="1" y2="0">
        <stop offset="0" stop-color="#000" stop-opacity="0"/>
        <stop offset="1" stop-color="#000" stop-opacity="0.6"/>
      </linearGradient>
    </defs>
    <path d="M540 553 C780 525 1000 470 1200 405 L1200 553 Z" fill="url(#curlShadow)" opacity="0.5"/>
    <path d="M1102 356 C1150 362 1185 388 1200 413 L1200 395 C1180 370 1150 356 1102 356 Z" fill="#1b1b1b" opacity="0.6"/>
    <path d="M560 553 C800 522 1000 470 1200 413 L1200 553 Z" fill="#ffffff"/>
    <path d="M850 500 C950 470 1050 420 1102 356 C1150 362 1185 388 1200 413 C1060 456 950 484 850 500 Z" fill="url(#flapShade)"/>
  </svg>

  <div class="brand">
    <div class="brand-name">LunaTessa</div>
    <div class="brand-tagline">Rewoven Kindness</div>
  </div>

</div>
</body>
</html>
```